Modern Business Card

Modern professional business card with more than just logo and demographic info. Something memorable.

We are a trendy/modern chiropractic group with an emphasis on neurology, hence the minimalist-type brain logo. We want to convey that modern and technical aspect with professionalism and the elite nature of our practice environment.

```html
<!DOCTYPE html>
<html lang="en">
<head>
<meta charset="utf-8">
<title>Keystone Spine – Business Card</title>
<link href="https://fonts.googleapis.com/css2?family=Roboto:wght@400;500&display=swap" rel="stylesheet">
<style>
  :root {
    --page-bg: #ffffff;
    --card-white: #fdfdfd;
    --brand-blue: #4a7fc1;
    --texture-light: #5289ca;
    --texture-dark: #3f74b8;
    --swoosh-grey: #6e6e6e;
    --text-grey: #5f5f5f;
    --text-dark: #1c1c1c;
    --white: #ffffff;
  }
  * { margin: 0; padding: 0; box-sizing: border-box; }
  html, body {
    width: 1200px; height: 1200px; overflow: hidden;
    background: var(--page-bg);
    font-family: "Roboto", Arial, sans-serif;
  }
  .canvas { position: relative; width: 1200px; height: 1200px; }

  .card { position: absolute; overflow: hidden; }
  .card-front {
    left: 232px; top: 173px; width: 705px; height: 408px;
    background: var(--card-white);
    border: 1px solid #ececec;
  }
  .card-back {
    left: 231px; top: 629px; width: 702px; height: 400px;
    background: var(--brand-blue);
  }
  .back-texture {
    position: absolute; inset: 0;
    background: linear-gradient(135deg, var(--texture-light) 0%, var(--brand-blue) 50%, var(--texture-dark) 100%);
  }

  .holder-name {
    position: absolute; left: 51px; top: 50px;
    font-size: 34px; font-weight: 500; color: var(--brand-blue);
  }
  .holder-role {
    position: absolute; left: 51px; top: 89px;
    font-size: 21px; font-weight: 400; color: var(--text-grey);
  }
  .address {
    position: absolute; left: 44px; top: 182px;
    font-size: 19.5px; line-height: 24px; color: var(--text-grey);
  }
  .contact-list {
    position: absolute; left: 44px; top: 271px; list-style: none;
  }
  .contact-list li {
    display: flex; align-items: center; height: 26px;
    font-size: 19.5px; color: var(--text-grey); white-space: nowrap;
  }
  .contact-list svg { width: 20px; height: 20px; margin-right: 14px; fill: var(--brand-blue); }

  .brand-mark {
    position: absolute; display: flex; align-items: center;
    font-weight: 500; letter-spacing: 1px; white-space: nowrap;
  }
  .brand-front {
    left: 358px; top: 183px; font-size: 28px; color: var(--text-dark);
  }
  .brand-front .brand-dot { width: 36px; height: 36px; border-radius: 50%; background: var(--brand-blue); margin-right: 14px; }
  .brand-back {
    left: 0; right: 0; top: 170px; justify-content: center;
    font-size: 50px; color: var(--white);
  }
  .brand-back .brand-dot { width: 56px; height: 56px; border-radius: 50%; background: var(--white); margin-right: 24px; }

  .footer-wave { position: absolute; left: 0; bottom: 0; width: 705px; height: 80px; }
  .website {
    position: absolute; right: 42px; bottom: 27px;
    font-size: 18.5px; color: var(--white);
  }
</style>
</head>
<body>
<main class="canvas">

  <section class="card card-front" aria-label="Business card front">
    <h1 class="holder-name">Marlen Voss</h1>
    <p class="holder-role">President</p>

    <p class="address">48 Harbor Lane 210<br>Portland OR 97201</p>

    <ul class="contact-list">
      <li>
        <svg viewBox="0 0 24 24" aria-hidden="true"><path d="M6.6 10.8a15.1 15.1 0 0 0 6.6 6.6l2.2-2.2c.3-.3.7-.4 1-.2 1.1.4 2.3.6 3.6.6.6 0 1 .4 1 1V20c0 .6-.4 1-1 1A17 17 0 0 1 3 4c0-.6.4-1 1-1h3.5c.6 0 1 .4 1 1 0 1.3.2 2.5.6 3.6.1.3 0 .7-.2 1z"/></svg>
        014 5562 3081
      </li>
      <li>
        <svg viewBox="0 0 24 24" aria-hidden="true"><path d="M7 2h10v5H7zM4 8h16a2 2 0 0 1 2 2v6h-4v-3H6v3H2v-6a2 2 0 0 1 2-2zm3 7h10v7H7z"/></svg>
        014 5562 3099
      </li>
      <li>
        <svg viewBox="0 0 24 24" aria-hidden="true"><path d="M2 5h18v2l-9 6-9-6zm0 4 9 6 9-6v3.5a6 6 0 0 0-7.7 6.5H2z"/><circle cx="18.5" cy="18.5" r="4.5"/></svg>
        info@kstspine.com
      </li>
    </ul>

    <div class="brand-mark brand-front">
      <span class="brand-dot"></span>KEYSTONE SPINE
    </div>

    <svg class="footer-wave" viewBox="0 0 705 80" preserveAspectRatio="none" aria-hidden="true">
      <path d="M0 80 L0 70 C180 25 430 -2 705 10 L705 14 C440 4 220 30 55 80 Z" fill="var(--swoosh-grey)"/>
      <path d="M55 80 C220 34 440 8 705 16 L705 80 Z" fill="var(--brand-blue)"/>
    </svg>
    <p class="website">www.kstspine.com</p>
  </section>

  <section class="card card-back" aria-label="Business card back">
    <div class="back-texture" role="img" aria-label="Fine diagonal stripe texture in blue tones"></div>
    <div class="brand-mark brand-back">
      <span class="brand-dot"></span>KEYSTONE SPINE
    </div>
  </section>

</main>
</body>
</html>
```